Request for Business Card Design

Hi. My name is Marlene, I am looking for a new business card design for my company, Quarrow Signal Instruments, LLC. I really like the design you did for Tarsel Venture and was hoping you could do something similar using our full logo and our mark. I am also open to any raised texture design using our mark. I have attached our full logo, which would need to be somewhere on the card, as well as the mark in both outline and full form, as well as our brand colors / guide. The card does not have to be white, as long as our logo and mark appear. I actually like darker colored business cards more, but am open to all options. If you are interested in working with me, please let me know. We would also take the business card design into letterhead design if you can do that.

```html
<!DOCTYPE html>
<html lang="en">
<head>
<meta charset="utf-8">
<title>Quarrow Signal Instruments – Business Card</title>
<link rel="stylesheet" href="https://fonts.googleapis.com/css2?family=Montserrat:wght@800&family=Open+Sans:wght@400;600;700&display=swap">
<style>
  :root {
    --bg: #222223;
    --card: #3a3a3c;
    --card-dark: #2c2c2e;
    --pattern-light: #8a8a8c;
    --blue: #1f9cc9;
    --white: #ffffff;
    --shadow: rgba(0,0,0,0.55);
  }
  * { margin: 0; padding: 0; box-sizing: border-box; }
  html, body { width: 1200px; height: 780px; overflow: hidden; background: var(--bg); }
  body { position: relative; font-family: "Open Sans", Arial, sans-serif; color: var(--white); }

  .card {
    position: absolute; top: 75px; width: 360px; height: 630px;
    border-radius: 26px; background: var(--card); overflow: hidden;
    box-shadow: 0 18px 40px var(--shadow);
  }
  .card--back { left: 200px; }
  .card--front { left: 640px; }

  .back-pattern {
    position: absolute; inset: 0;
    background: linear-gradient(160deg, var(--pattern-light) 0%, #55555a 28%, var(--card) 55%, var(--card-dark) 100%);
  }
  .back-brand {
    position: absolute; top: 34px; right: 30px;
    display: flex; align-items: center; gap: 8px;
  }
  .back-brand .brand-dot { width: 16px; height: 16px; border-radius: 50%; background: var(--blue); }
  .back-brand .brand-name { font-weight: 700; font-size: 11px; letter-spacing: 1.5px; color: var(--white); }

  .front-brand {
    position: absolute; top: 62px; left: 42px;
    display: flex; align-items: center; gap: 14px;
  }
  .front-brand .brand-dot { width: 44px; height: 44px; border-radius: 50%; background: var(--blue); }
  .front-brand .brand-name { font-weight: 700; font-size: 15px; letter-spacing: 1.6px; line-height: 1.3; color: var(--white); }

  .person { position: absolute; top: 318px; left: 0; width: 100%; text-align: center; }
  .person-name { font-family: "Montserrat", Arial, sans-serif; font-weight: 800; font-size: 34px; color: var(--blue); line-height: 1; }
  .person-role { font-weight: 600; font-size: 14px; margin-top: 4px; }

  .contact-frame { position: absolute; left: 0; top: 388px; width: 360px; height: 140px; }

  .contact-list {
    position: absolute; top: 426px; left: 0; width: 100%;
    list-style: none; text-align: center; font-size: 13.5px; line-height: 22px;
  }

  .address { position: absolute; top: 530px; left: 0; width: 100%; text-align: center; }
  .address svg { display: block; margin: 0 auto 8px; }
  .address p { font-size: 14px; line-height: 20px; }
</style>
</head>
<body>

  <section class="card card--back" aria-label="Card back">
    <div class="back-pattern" role="img" aria-label="Repeating brand mark pattern with a raised gloss finish"></div>
    <div class="back-brand">
      <span class="brand-dot"></span>
      <span class="brand-name">QUARROW</span>
    </div>
  </section>

  <section class="card card--front" aria-label="Card front">
    <div class="front-brand">
      <span class="brand-dot"></span>
      <span class="brand-name">QUARROW<br>SIGNAL INSTRUMENTS</span>
    </div>

    <div class="person">
      <h1 class="person-name">Marlene</h1>
      <p class="person-role">Director</p>
    </div>

    <svg class="contact-frame" viewBox="0 0 360 140" aria-hidden="true">
      <g fill="none" stroke="var(--blue)" stroke-width="2">
        <polyline points="100,17 22,17 22,112 48,112"/>
        <polyline points="262,17 336,17 336,92 318,92"/>
        <polyline points="140,30 62,30 62,50 78,50"/>
        <polyline points="222,30 296,30 296,70 282,70"/>
      </g>
      <g fill="var(--blue)">
        <polygon points="48,107 56,112 48,117"/>
        <polygon points="318,87 310,92 318,97"/>
        <polygon points="78,45 86,50 78,55"/>
        <polygon points="282,65 274,70 282,75"/>
      </g>
      <g fill="var(--blue)">
        <circle cx="113" cy="17" r="12"/>
        <circle cx="158" cy="17" r="12"/>
        <circle cx="203" cy="17" r="12"/>
        <circle cx="248" cy="17" r="12"/>
      </g>
      <g fill="none" stroke="var(--white)" stroke-width="1.5">
        <rect x="106" y="12" width="14" height="10"/>
        <polyline points="106,12 113,18 120,12"/>
        <path d="M152 11 q-2 6 3 11 q5 4 10 2 l-2 -3 l-3 1 q-4 -2 -5 -6 l2 -2 z"/>
        <rect x="197" y="14" width="12" height="9"/>
        <rect x="199" y="10" width="8" height="4"/>
        <circle cx="248" cy="17" r="6"/>
        <line x1="242" y1="17" x2="254" y2="17"/>
        <ellipse cx="248" cy="17" rx="2.5" ry="6"/>
      </g>
    </svg>

    <ul class="contact-list">
      <li>+001 555 210 4827</li>
      <li>+001 555 210 4830</li>
      <li>info@quarrowsignal.com</li>
      <li>www.quarrowsignal.com</li>
    </ul>

    <div class="address">
      <svg width="26" height="26" viewBox="0 0 26 26" aria-hidden="true">
        <circle cx="13" cy="13" r="13" fill="var(--blue)"/>
        <path d="M13 6 a5 5 0 0 1 5 5 c0 4 -5 9 -5 9 s-5 -5 -5 -9 a5 5 0 0 1 5 -5 z" fill="none" stroke="var(--white)" stroke-width="1.5"/>
        <circle cx="13" cy="11" r="1.8" fill="var(--white)"/>
      </svg>
      <p>1180 Harbor Reach Drive</p>
      <p>Fairlow, CO 80999</p>
    </div>
  </section>

</body>
</html>
```